New Fun, Positive, energised looking Business Card Needed for High Achiever Coach

I am looking for a two sided full colour business card. I am self employed and have recently re branded my 1-2-1 work Restoring Energy for Leaders. My target client base for these cards is therefore high achievers - usually aged 40 -55, they are often entrepreneurs, CEO or work in banking and finance and 2/3 are male. I work with them on 90 day or 6 month coaching programs to help them live their success in a healthier, more sustainable and fulfiiled way. They pay for this privately so though they are corporate types the cards need not look 'corporate'. I want to portray the idea of transformation, vitality and re-connecting.
You can get a feel for the look I like on my new website: morvenlisk.co.uk
I want to use this logo with strapline (Restoring Energy for Leaders) (I purchased off Logoharbor) and font/ colours (the turquoise and green).
Details to include on the card:
www.morvenlisk.co.uk
+44 7915 302618
morven@morvenlisk.co.uk
skype: morvenlisk
I'd also like to include:
Do you struggle to switch off? Want to be healthier and feel fitter? Want closer relationships? More clarity over the direction you are headed? I can help you do these things using integrated mind-body techniques. Visit morvenlisk.co.uk TODAY to apply for a FREE Breakthrough session.
BUT if that is too much text for a card I am open to advice/ammendments.
Updates
Thanks for your design - I am considering them. PLease change the wording to :

```html
<!DOCTYPE html>
<html lang="en">
<head>
<meta charset="utf-8">
<title>Morven Lisk – Business Card</title>
<link rel="stylesheet" href="https://fonts.googleapis.com/css2?family=Open+Sans:wght@400;700&family=Alfa+Slab+One&family=Dancing+Script:wght@500&display=swap">
<style>
  :root {
    --backdrop: #3a3a3a;
    --card-white: #ffffff;
    --card-shade: #eeeeee;
    --turquoise: #0aa0c9;
    --turquoise-deep: #0a87a8;
    --green: #4caf50;
    --green-deep: #2f8f3a;
    --green-light: #5fbf63;
    --ink: #2b2b2b;
  }
  * { margin: 0; padding: 0; box-sizing: border-box; }
  html, body { width: 1200px; height: 900px; overflow: hidden; }
  body {
    background: var(--backdrop);
    display: flex;
    align-items: center;
    justify-content: center;
    gap: 48px;
    font-family: "Open Sans", Arial, sans-serif;
  }
  .card {
    position: relative;
    width: 520px;
    height: 336px;
    border-radius: 22px;
    overflow: hidden;
  }

  /* Front */
  .card-front {
    background: linear-gradient(135deg, var(--card-white) 55%, var(--card-shade));
  }
  .brand {
    position: absolute;
    left: 42px;
    top: 40px;
    display: flex;
    align-items: center;
    gap: 22px;
  }
  .brand-dot {
    width: 60px;
    height: 60px;
    border-radius: 50%;
    background: var(--green);
    flex: none;
  }
  .brand-name {
    font-family: "Alfa Slab One", Georgia, serif;
    font-weight: 400;
    font-size: 44px;
    color: var(--turquoise);
    letter-spacing: 0.5px;
    line-height: 1;
  }
  .strapline {
    position: absolute;
    left: 122px;
    top: 106px;
    font-family: "Dancing Script", cursive;
    font-weight: 500;
    font-size: 28px;
    color: var(--turquoise);
    white-space: nowrap;
  }
  .contacts {
    position: absolute;
    left: 0;
    right: 0;
    top: 184px;
    display: grid;
    grid-template-columns: auto auto;
    justify-content: center;
    column-gap: 20px;
    row-gap: 6px;
    font-size: 15px;
    color: var(--ink);
  }
  .contact { display: flex; align-items: center; gap: 5px; white-space: nowrap; }
  .contact svg { width: 13px; height: 13px; fill: var(--turquoise); flex: none; }
  .contact-dot {
    width: 12px; height: 12px; border-radius: 50%;
    background: var(--turquoise); flex: none;
  }
  .wave { position: absolute; left: 0; bottom: 0; width: 520px; height: 110px; }

  /* Back */
  .card-back {
    background: radial-gradient(ellipse at 45% 35%, var(--green-light), var(--green) 55%, var(--green-deep));
    display: flex;
    align-items: center;
    justify-content: center;
    gap: 18px;
  }
  .back-dot {
    width: 40px; height: 40px; border-radius: 50%;
    background: var(--card-white);
  }
  .back-name {
    font-family: "Alfa Slab One", Georgia, serif;
    font-weight: 400;
    font-size: 38px;
    color: var(--card-white);
    letter-spacing: 0.5px;
  }
</style>
</head>
<body>
  <section class="card card-front" aria-label="Business card front">
    <div class="brand">
      <span class="brand-dot"></span>
      <span class="brand-name">Morven Lisk</span>
    </div>
    <p class="strapline">Restoring Energy for Leaders</p>

    <div class="contacts">
      <span class="contact">
        <svg viewBox="0 0 16 16" aria-hidden="true"><path d="M3.6 1.2l2.3 2.6-1.3 1.8c.9 2 2.5 3.7 4.5 4.6l1.8-1.3 2.6 2.3-1.2 2.4C7.4 13.8 2.2 8.6 1.3 3.6z"/></svg>
        +44 7915 302618
      </span>
      <span class="contact">
        <svg viewBox="0 0 16 16" aria-hidden="true"><path d="M8 1a7 7 0 100 14A7 7 0 008 1zm0 1.4c.8 0 1.7 1.5 2 3.8H6c.3-2.3 1.2-3.8 2-3.8zM2.5 7.3h2.6c0 .5 0 1 .1 1.4H2.5a5.6 5.6 0 010-1.4zm8.4 0h2.6a5.6 5.6 0 010 1.4h-2.7c.1-.4.1-.9.1-1.4zM6 9.8h4c-.3 2.3-1.2 3.8-2 3.8s-1.7-1.5-2-3.8z"/></svg>
        www.morvenlisk.co.uk
      </span>
      <span class="contact">
        <svg viewBox="0 0 16 16" aria-hidden="true"><path d="M1 3h14v10H1zm1.4 1.4L8 8.5l5.6-4.1z"/></svg>
        morven@morvenlisk.co.uk
      </span>
      <span class="contact">
        <span class="contact-dot"></span>
        morvenlisk
      </span>
    </div>

    <svg class="wave" viewBox="0 0 520 110" preserveAspectRatio="none" aria-hidden="true">
      <defs>
        <linearGradient id="bandGrad" x1="0" x2="1" y1="0" y2="0">
          <stop offset="0" stop-color="#0a87a8"/>
          <stop offset="0.5" stop-color="#0aa0c9"/>
          <stop offset="1" stop-color="#0a87a8"/>
        </linearGradient>
      </defs>
      <path d="M0 42 C140 28 300 30 470 52 C300 38 140 40 0 48 Z" fill="#4caf50"/>
      <path d="M0 58 C160 48 330 64 520 48 L520 110 L0 110 Z" fill="url(#bandGrad)"/>
    </svg>
  </section>

  <section class="card card-back" aria-label="Business card back">
    <span class="back-dot"></span>
    <span class="back-name">Morven Lisk</span>
  </section>
</body>
</html>
```